Business cards for KORU Real Estate Holdings LLC

We need a cool, original business card design for a company based in the Washington DC metropolitan area. We are a new energetic and passionate Real Estate Investing Company that invests in all types of real estate; commercial, residential, industrial etc.

Our company color is Red since it reflects action, energy and speed; it is assertive confident, energizing, exciting, powerful, passionate and determined. So we would like business card communicate those qualities to the audience.

Our audiences are investors that want to invest with us, real estate sellers, buyers, and tenants who lease from us.

Our logo is attached

```html
<!DOCTYPE html>
<html lang="en">
<head>
<meta charset="utf-8">
<title>KORU — Business Cards</title>
<link href="https://fonts.googleapis.com/css2?family=Open+Sans:wght@400;600;700&display=swap" rel="stylesheet">
<style>
  :root {
    --backdrop: #d8d4cf;
    --card-dark: #1f1d1e;
    --card-light: #ebe8e3;
    --accent-red: #e0243c;
    --accent-orange: #e8a23a;
    --ink: #3a3838;
    --ink-soft: #6b6868;
    --white: #ffffff;
  }
  * { box-sizing: border-box; margin: 0; padding: 0; }
  html, body {
    width: 1151px; height: 1200px; overflow: hidden;
    background: var(--backdrop);
    font-family: "Open Sans", sans-serif;
    color: var(--ink);
  }
  .card {
    position: absolute; left: 187px; width: 776px; height: 450px;
    background: var(--card-light);
    box-shadow: 0 10px 30px rgba(0,0,0,.18);
    overflow: hidden;
  }
  .card--front { top: 133px; }
  .card--back { top: 700px; }
  .band {
    position: absolute; left: 0; top: 0; width: 100%;
    background: var(--card-dark);
    border-bottom: 5px solid var(--accent-red);
  }
  .card--front .band { height: 210px; }
  .card--back .band { height: 212px; }

  .brand {
    position: absolute; left: 0; right: 0; top: 0; height: 205px;
    display: flex; align-items: center; justify-content: center; gap: 16px;
  }
  .brand__dot { width: 34px; height: 34px; border-radius: 50%; background: var(--accent-red); }
  .brand__name {
    font-weight: 700; font-size: 56px; letter-spacing: 3px; color: var(--white); line-height: 1;
  }

  .info { position: absolute; left: 0; top: 0; width: 776px; height: 450px; }
  .person { position: absolute; left: 100px; top: 250px; }
  .person__name { font-size: 24px; color: var(--ink); font-weight: 400; line-height: 1.1; }
  .person__first { color: var(--accent-red); font-weight: 600; }
  .person__title { font-size: 15px; color: var(--ink-soft); margin-top: 4px; padding-left: 18px; }

  .divider {
    position: absolute; left: 387px; top: 248px; width: 2px; height: 150px;
    background: linear-gradient(to bottom, transparent, var(--ink) 30%, var(--ink) 70%, transparent);
  }
  .contact { position: absolute; left: 446px; top: 246px; list-style: none; font-size: 16px; line-height: 24px; color: var(--ink); }
  .contact__item { display: flex; align-items: center; gap: 10px; white-space: nowrap; }
  .contact__item--plain { gap: 0; }
  .contact__icon { width: 14px; height: 14px; flex: none; }

  .web {
    position: absolute; left: 0; right: 0; top: 92px; text-align: center;
    font-size: 17px; letter-spacing: 4px; color: var(--white);
  }
  .web__domain { color: var(--accent-orange); }

  .show-through { transform: scaleX(-1); opacity: .32; }
</style>
</head>
<body>

<section class="card card--front" aria-label="Business card front">
  <div class="band">
    <div class="brand">
      <span class="brand__dot"></span>
      <span class="brand__name">KORU</span>
    </div>
  </div>
  <div class="info">
    <div class="person">
      <p class="person__name"><span class="person__first">Marcus</span> Hale</p>
      <p class="person__title">Owner / C.E.O.</p>
    </div>
    <div class="divider"></div>
    <ul class="contact">
      <li class="contact__item contact__item--plain">2150 Larkin Avenue</li>
      <li class="contact__item contact__item--plain">Suite # 410</li>
      <li class="contact__item">
        <svg class="contact__icon" viewBox="0 0 14 14"><circle cx="7" cy="7" r="7" fill="#3a3838"/><path d="M4.5 3.5l1.5 1.6-.8 1c.5 1 1.2 1.7 2.2 2.2l1-.8 1.6 1.5-.9 1.1C6.5 10 4 7.5 3.4 4.4z" fill="#fff"/></svg>
        202-555-0148</li>
      <li class="contact__item">
        <svg class="contact__icon" viewBox="0 0 14 14"><circle cx="7" cy="7" r="7" fill="#3a3838"/><rect x="4" y="5" width="6" height="5" fill="#fff"/><rect x="5" y="3" width="4" height="2.5" fill="#fff"/></svg>
        202-555-0172</li>
      <li class="contact__item">
        <svg class="contact__icon" viewBox="0 0 14 14"><circle cx="7" cy="7" r="7" fill="#3a3838"/><rect x="5" y="3" width="4" height="8" rx="1" fill="#fff"/></svg>
        202-555-0196</li>
      <li class="contact__item">
        <svg class="contact__icon" viewBox="0 0 14 14"><rect x="1" y="3" width="12" height="8" fill="#3a3838"/><path d="M1 3l6 4.5L13 3" stroke="#fff" fill="none"/></svg>
        info@koruhold.com</li>
      <li class="contact__item">
        <svg class="contact__icon" viewBox="0 0 14 14"><rect x="1" y="9" width="3" height="3" fill="#3a3838"/><rect x="5.5" y="6" width="3" height="6" fill="#3a3838"/><rect x="10" y="3" width="3" height="9" fill="#3a3838"/></svg>
        www.koruhold.com</li>
    </ul>
  </div>
</section>

<section class="card card--back" aria-label="Business card back">
  <div class="info show-through" aria-hidden="true">
    <div class="person" style="top:238px">
      <p class="person__name"><span class="person__first">Marcus</span> Hale</p>
      <p class="person__title">Owner / C.E.O.</p>
    </div>
    <div class="divider" style="top:236px"></div>
    <ul class="contact" style="top:234px">
      <li class="contact__item contact__item--plain">2150 Larkin Avenue</li>
      <li class="contact__item contact__item--plain">Suite # 410</li>
      <li class="contact__item"><svg class="contact__icon" viewBox="0 0 14 14"><circle cx="7" cy="7" r="7" fill="#3a3838"/></svg>202-555-0148</li>
      <li class="contact__item"><svg class="contact__icon" viewBox="0 0 14 14"><circle cx="7" cy="7" r="7" fill="#3a3838"/></svg>202-555-0172</li>
      <li class="contact__item"><svg class="contact__icon" viewBox="0 0 14 14"><circle cx="7" cy="7" r="7" fill="#3a3838"/></svg>202-555-0196</li>
      <li class="contact__item"><svg class="contact__icon" viewBox="0 0 14 14"><rect x="1" y="3" width="12" height="8" fill="#3a3838"/></svg>info@koruhold.com</li>
      <li class="contact__item"><svg class="contact__icon" viewBox="0 0 14 14"><rect x="1" y="9" width="3" height="3" fill="#3a3838"/><rect x="5.5" y="6" width="3" height="6" fill="#3a3838"/><rect x="10" y="3" width="3" height="9" fill="#3a3838"/></svg>www.koruhold.com</li>
    </ul>
  </div>
  <div class="band">
    <p class="web">www.<span class="web__domain">KoruHold</span>.com</p>
  </div>
</section>

</body>
</html>
```